Construction company stationary design

We're wanting to develop a new professional stationary set for a newly establised property related business using our existing logo (attached). Business incorporates renovations, property investment and property development.

Specifically needing letter head, business cards, envelopes, email signature and need to get tshirt and caps embroydered.

Looking for something quite modern but professional using white, black and green.

Investment

```html
<!DOCTYPE html>
<html lang="en">
<head>
<meta charset="utf-8">
<title>Kelt Builders Stationery</title>
<link href="https://fonts.googleapis.com/css2?family=Arimo:wght@400;700&family=Open+Sans:wght@400;700&display=swap" rel="stylesheet">
<style>
  :root {
    --backdrop: #ececec;
    --paper: #ffffff;
    --brand-green: #7ab929;
    --ink-dark: #555555;
    --ink-soft: #8a8a8a;
    --rule: #9a9a9a;
    --cell-fill: #e9e9e9;
  }
  * { box-sizing: border-box; margin: 0; padding: 0; }
  html, body { width: 1200px; height: 815px; overflow: hidden; }
  body {
    position: relative;
    background: var(--backdrop);
    font-family: "Open Sans", sans-serif;
    color: var(--ink-soft);
  }
  .sheet {
    position: absolute;
    top: 70px;
    width: 484px;
    height: 685px;
    background: var(--paper);
  }
  .sheet--letterhead { left: 80px; }
  .sheet--fax { left: 638px; }

  .brand-name {
    position: absolute;
    color: var(--brand-green);
    font-family: "Open Sans", sans-serif;
    font-weight: 700;
    font-size: 19px;
    line-height: 1.05;
    letter-spacing: 0.5px;
  }
  .sheet--letterhead .brand-name { left: 47px; top: 74px; width: 110px; }
  .sheet--fax .brand-name { right: 24px; top: 84px; width: 110px; text-align: right; }

  .accent-band {
    position: absolute;
    right: 0;
    bottom: 0;
    width: 206px;
    height: 10px;
    background: var(--brand-green);
  }
  .sheet--fax .accent-band { width: 225px; }

  .footer-col {
    position: absolute;
    top: 647px;
    height: 38px;
    border-left: 1px solid #c8c8c8;
    padding-left: 10px;
    font-size: 6.5px;
    line-height: 10px;
    color: var(--ink-soft);
  }
  .footer-col strong, .contact strong, .web strong { color: var(--brand-green); font-weight: 700; }
  .footer-col--address { left: 46px; }
  .footer-col--contact { left: 162px; }
  .footer-col--web { left: 266px; }
  .sheet--fax .footer-col--web { left: 248px; top: 647px; }

  .fax-title {
    position: absolute;
    left: 22px;
    top: 70px;
    font-family: "Arimo", sans-serif;
    font-size: 60px;
    line-height: 1;
    color: var(--ink-dark);
  }
  .contact {
    position: absolute;
    right: 154px;
    top: 87px;
    text-align: right;
    font-size: 6.5px;
    line-height: 9px;
    color: var(--ink-soft);
  }

  .details {
    position: absolute;
    left: 25px;
    top: 164px;
    width: 436px;
    border-collapse: collapse;
    font-family: "Arimo", sans-serif;
    font-size: 7.5px;
    color: #444;
  }
  .details td {
    border: 1px solid var(--rule);
    height: 14.5px;
    padding: 0 4px;
    font-weight: 700;
  }
  .details .label { width: 46px; }
  .details .value { width: 172px; }

  .comments-box {
    position: absolute;
    left: 25px;
    top: 251px;
    width: 436px;
    height: 382px;
    border: 1px solid var(--rule);
    font-family: "Arimo", sans-serif;
  }
  .flags { display: flex; height: 15px; background: var(--cell-fill); border-bottom: 1px solid var(--rule); }
  .flag {
    display: flex;
    align-items: center;
    justify-content: center;
    gap: 4px;
    border-right: 1px solid var(--rule);
    font-size: 7.5px;
    font-weight: 700;
    color: #444;
  }
  .flag:last-child { border-right: none; }
  .flag::before { content: ""; width: 5px; height: 5px; border: 1px solid #777; background: #fff; }
  .comments-label {
    text-align: center;
    font-size: 7.5px;
    color: #444;
    margin-top: 11px;
  }
</style>
</head>
<body>

<section class="sheet sheet--letterhead" aria-label="Letterhead">
  <div class="brand-name">KELT<br>BUILDERS</div>
  <div class="footer-col footer-col--address">418 Ridgeview Ct. Suite 210<br>Fairmont Springs, CO 80000</div>
  <div class="footer-col footer-col--contact"><strong>Phone:</strong> (555) 310-7788<br><strong>Email:</strong> hello@keltbuilders.com</div>
  <div class="footer-col footer-col--web web">www.<strong>keltbuilders</strong>.com</div>
  <div class="accent-band"></div>
</section>

<section class="sheet sheet--fax" aria-label="Fax cover sheet">
  <h1 class="fax-title">FAX</h1>
  <div class="contact">
    418 Ridgeview Ct. Suite 210<br>
    Fairmont Springs, CO 80000<br>
    <strong>Phone:</strong> (555) 310-7788<br>
    <strong>Email:</strong> hello@keltbuilders.com
  </div>
  <div class="brand-name">KELT<br>BUILDERS</div>

  <table class="details">
    <tr><td class="label">To:</td><td class="value"></td><td class="label">From:</td><td class="value"></td></tr>
    <tr><td class="label">Fax:</td><td class="value"></td><td class="label">Pages:</td><td class="value"></td></tr>
    <tr><td class="label">Phone:</td><td class="value"></td><td class="label">Date:</td><td class="value"></td></tr>
    <tr><td class="label">Re:</td><td class="value"></td><td class="label">CC:</td><td class="value"></td></tr>
  </table>

  <div class="comments-box">
    <div class="flags">
      <span class="flag" style="width:88px">Urgent</span>
      <span class="flag" style="width:82px">For Review</span>
      <span class="flag" style="width:97px">Please Comment</span>
      <span class="flag" style="width:82px">Please Reply</span>
      <span class="flag" style="width:87px">Confidential</span>
    </div>
    <p class="comments-label">COMMENTS:</p>
  </div>

  <div class="footer-col footer-col--web web">www.<strong>keltbuilders</strong>.com</div>
  <div class="accent-band"></div>
</section>

</body>
</html>
```